New word press website site design

We provide email marketing to aircraft brokers and dealers to assist in finding buyers for their aircraft.

Our target market to purchase our broadcasts are the aircraft sellers – NOT the buyers.

Our target market when sending the email broadcast, are the buyers (end users).

The website should target brokers and our email database targets the buyers.

We do not buy or sell aircraft as a company. We provide email marketing solutions to connect buyers and sellers of aircraft.

Our other site is planelantern.com and will be redesigned soon. Please use it as a reference as far as general scope but they layout can be completely different and should include helicopters only as far as imagery. The colors should be similar as the logos are similar, however we do NOT want both sites to be identical in use of primary color

Plenty of images and sample broadcasts attached to use as needed throughout the site.

Headlines listed below with some text copy.

In the event that we need to add more text, please use standard greek text as a place holder for the purposes of the mockup design.

Need to have a “SUBSCRIBE” button to join our mailing list.

Possible Headlines:

Exclusively Showcasing Rotor Wing Aircraft to the Global Marketplace

Showcasing Pre-Owned Helicopters Available For Sale, Lease, Trade, or Wanted for Acquisition.

Mobile-optimized Email Campaigns that Render Correctly Across all Devices

Targeted worldwide recipients that currently own, operate, or have an interest in rotor wing aircraft

STRONGEST Rotor Wing Database in the Industry

Text/Copy:

HOME
Rotorbay Vista is one of most powerful marketing tools in the industry to utilize in reaching targeted buyers of pre-owned helicopters. Rotorbay Vista provides the rotor wing aircraft market with a fast, effective, and affordable email broadcast solution to utilize in the marketing of Helicopters for sale.

Developed Exclusively to Showcase Rotor Wing Aircraft to the Global marketplace, Rotorbay Vista is a powerful tool designed to maximize leads and accelerate the sales process by providing the ability to reach a global network of Helicopter buyers in a matter of seconds.

DATABASE:

While Rotorbay Vista is delivered to all known broker/dealers, our primary focus is in reaching end users. Our opt-in/opt-out recipient database is updated daily and developed specifically to deliver the latest details on helicopters available for sale or lease to the inboxes of a global network of Helicopter buyers and sellers.

· Helicopter Owners

· Helicopter Operators

· Helicopter Charter Services

· Helicopter Management Companies

· Corporate/Municipal Flight Departments

· Helicopter Pilots

· Senior Aviation Executives

· Wealth Management Firms

· High Net Worth Individuals

· Helicopter Broker/Dealers

Helicopter Tour/Travel Firms

· Off Shore Oil & Gas Production Firms

· Municipalities/Media/Medevac Firms

Our recipient database is continuously updated and developed specifically to reach buyers and sellers of Helicopters. This ensures that your Helicopter will be showcased to the right people. Rotorbay Vista does not broadcast non-rotor wing aircraft and focuses exclusively on the Global Helicopter Market.

Broadcast Design:

Rotorbay Vista broadcast ads are custom designed for you by incorporating your corporate image and branding. Because you have worked hard in developing your corporate image, we strive to maintain it while designing an ad that will showcase your Helicopter to its best advantage. Rotorbay Vista utilizes Mobile-optimized Email Campaigns with Responsive Coding to render correctly across all devices

Once you have approved the design, we schedule the broadcast to be sent on the available date and time you request. The broadcast will link to your website and the results can be immediate. All email leads and replies will go to the email address that you provided.

Pricing:
Create a place holder for 3 Different Broadcast Packages

-Broadcast Package A
-Broadcast Package B
-Broadcast Package C

Target Market(s)

The target market is any person or company that has aircraft for sale. We work with brokers, dealers, and owners to assist in finding buyers for their aircraft using email marketing campaigns (Showcase broadcasts).

Industry/Entity Type

Aviation

Colors
0255a3
00a990

Requirements
Nice to have
• Samples of helicopter for sale broadcast ads in /image gallery/slider

```html
<!DOCTYPE html>
<html lang="en">
<head>
<meta charset="utf-8">
<title>Rotorline Media Inc – Rotorbay Vista</title>
<link rel="stylesheet" href="https://fonts.googleapis.com/css2?family=Lora:wght@400&family=Open+Sans:wght@400;600&display=swap">
<style>
:root{
  --page-bg:#333333;
  --panel:#ffffff;
  --brand-blue:#2166b0;
  --button-blue:#2f6db5;
  --cta-red:#c8102e;
  --text:#333333;
  --muted:#555555;
  --rule:#dddddd;
  --band:#ebebeb;
  --card-border:#cfcfcf;
  --footer-text:#aaaaaa;
}
*{box-sizing:border-box;margin:0;padding:0}
html,body{width:1200px;height:2975px;overflow:hidden}
body{background:var(--page-bg);font-family:"Open Sans",Arial,sans-serif;color:var(--text);position:relative}
.panel{position:absolute;left:190px;top:32px;width:820px;height:2849px;background:var(--panel)}
.masthead{height:101px;text-align:center;font-family:"Lora",Georgia,serif;font-size:49px;line-height:101px;color:var(--brand-blue);font-weight:400}
.hero{height:410px;background:linear-gradient(180deg,#3f6fd6 0%,#7fa3e6 35%,#c9d5e6 55%,#8a8a86 62%,#6e6d6a 100%);padding-top:26px;text-align:center}
.hero-title{color:#fff;font-weight:600;font-size:29px;line-height:38px}
.intro{height:609px;border-bottom:2px solid var(--rule);padding:16px 10px 0;text-align:center}
.gallery{display:grid;grid-template-columns:repeat(3,256px);gap:16px;height:165px}
.gallery-item{height:165px}
.gallery-item.sunset{background:linear-gradient(160deg,#f7c77a,#d9894a 55%,#6b4a3a)}
.gallery-item.helipad{background:linear-gradient(180deg,#3d72c9 0%,#9ec0ec 55%,#5f8a4c 70%,#4a4a4a 100%)}
.gallery-item.skyline{background:linear-gradient(180deg,#3a8ad0,#8fc2ea)}
.copy{font-size:16.5px;line-height:31px;color:var(--text);padding:0 22px}
.intro .copy:first-of-type{margin-top:34px}
.copy + .copy{margin-top:24px}
.btn{display:inline-block;font-family:"Open Sans",Arial,sans-serif;font-weight:600;color:#fff;text-decoration:none;text-transform:uppercase}
.btn-subscribe{background:var(--cta-red);width:224px;height:60px;line-height:60px;font-size:19px}
.intro .btn-subscribe{margin-top:34px}
.section-title{font-family:"Lora",Georgia,serif;font-weight:400;color:var(--brand-blue);font-size:32px;line-height:40px;text-align:center;text-transform:uppercase}
.database{height:859px;padding-top:73px;text-align:center}
.database .copy{margin-top:18px}
.audience{list-style:none;display:grid;grid-template-columns:432px 1fr;grid-auto-flow:column;grid-template-rows:repeat(7,51.5px);text-align:left;padding:26px 22px 0;font-family:"Lora",Georgia,serif;font-size:18.5px;color:var(--text)}
.audience li{line-height:51.5px}
.audience li::before{content:"• "}
.database .closing{margin-top:34px}
.pricing{height:511px;background:var(--band);padding-top:20px}
.packages{display:grid;grid-template-columns:repeat(3,244px);gap:24px;justify-content:center;margin-top:20px}
.package{height:369px;background:#fff;border:2px solid var(--card-border);text-align:center}
.package-head{height:128px;border-bottom:2px solid var(--card-border);padding-top:18px;font-family:"Lora",Georgia,serif}
.package-kicker{font-size:16px;line-height:20px;text-transform:uppercase}
.package-name{font-size:30px;line-height:36px}
.package-price{font-size:31px;line-height:40px;color:var(--brand-blue)}
.package-price small{font-size:18px}
.features{list-style:none;padding-top:22px;font-size:13px;line-height:27px;color:var(--muted)}
.btn-signup{background:var(--button-blue);width:144px;height:44px;line-height:44px;font-size:17px;margin-top:20px}
.contact{padding-top:47px;text-align:center}
.contact-title{font-family:"Lora",Georgia,serif;font-weight:400;font-size:33px;line-height:40px;color:var(--brand-blue)}
.address{font-family:"Lora",Georgia,serif;font-size:19px;line-height:28px;margin-top:7px}
.reach{font-family:"Lora",Georgia,serif;font-size:28px;line-height:40px;margin-top:2px;display:flex;justify-content:center;gap:38px}
.icon{display:inline-block;vertical-align:middle;fill:var(--text)}
.contact .btn-subscribe{margin-top:22px}
.site-footer{position:absolute;left:190px;top:2910px;width:820px;height:40px;display:flex;align-items:center;justify-content:space-between;color:var(--footer-text);font-size:13px}
.social{display:flex;gap:22px}
.social span{display:block;width:22px;height:22px;border-radius:50%;background:var(--footer-text)}
</style>
</head>
<body>
<main class="panel">
  <header class="masthead">Rotorline Media Inc</header>

  <section class="hero" role="img" aria-label="Red and silver helicopter parked on a yellow-marked helipad under a blue sky">
    <h1 class="hero-title">Exclusively Showcasing Rotor Wing Aircraft<br>to the Global Marketplace</h1>
  </section>

  <section class="intro">
    <div class="gallery">
      <div class="gallery-item sunset" role="img" aria-label="Helicopters flying at sunset"></div>
      <div class="gallery-item helipad" role="img" aria-label="Helicopter on a curved helipad"></div>
      <div class="gallery-item skyline" role="img" aria-label="Red and white medical helicopter in flight"></div>
    </div>
    <p class="copy">Rotorbay Vista is one of most powerful marketing tools in the industry to utilize in reaching targeted buyers of pre-owned helicopters. Rotorbay Vista provides the rotor wing aircraft market with a fast, effective, and affordable email broadcast solution to utilize in the marketing of Helicopters for sale.</p>
    <p class="copy">Developed Exclusively to Showcase Rotor Wing Aircraft to the Global marketplace, Rotorbay Vista is a powerful tool designed to maximize leads and accelerate the sales process by providing the ability to reach a global network of Helicopter buyers in a matter of seconds.</p>
    <a class="btn btn-subscribe" href="#">Subscribe Now</a>
  </section>

  <section class="database">
    <h2 class="section-title">Database</h2>
    <p class="copy">While Rotorbay Vista is delivered to all known broker/dealers, our primary focus is in reaching end users. Our opt-in/opt-out recipient database is updated daily and developed specifically to deliver the latest details on helicopters available for sale or lease to the inboxes of a global network of Helicopter buyers and sellers.</p>
    <ul class="audience">
      <li>Helicopter Owners</li>
      <li>Helicopter Operators</li>
      <li>Helicopter Charter Services</li>
      <li>Helicopter Management Companies</li>
      <li>Corporate/Municipal Flight Departments</li>
      <li>Helicopter Pilots</li>
      <li>Senior Aviation Executives</li>
      <li>Wealth Management Firms</li>
      <li>High Net Worth Individuals</li>
      <li>Helicopter Broker/Dealers</li>
      <li>Helicopter Tour/Travel Firms</li>
      <li>Off Shore Oil &amp; Gas Production Firms</li>
      <li>Municipalities/Media/Medevac Firms</li>
    </ul>
    <p class="copy closing">Our recipient database is continuously updated and developed specifically to reach buyers and sellers of Helicopters. This ensures that your Helicopter will be showcased to the right people. Rotorbay Vista does not broadcast non-rotor wing aircraft and focuses exclusively on the Global Helicopter Market.</p>
  </section>

  <section class="pricing">
    <h2 class="section-title">Pricing</h2>
    <div class="packages">
      <article class="package">
        <div class="package-head">
          <div class="package-kicker">Broadcast</div>
          <div class="package-name">Package A</div>
          <div class="package-price">$25<small>/mo</small></div>
        </div>
        <ul class="features">
          <li>Vestibulum pharetra diam</li><li>Mauris placerat eros</li><li>Donec a nisl vel ante tristique</li><li>Praesent accumsan nunc</li><li>Sed quis metus nibh</li>
        </ul>
        <a class="btn btn-signup" href="#">Sign Up Now</a>
      </article>
      <article class="package">
        <div class="package-head">
          <div class="package-kicker">Broadcast</div>
          <div class="package-name">Package B</div>
          <div class="package-price">$30<small>/mo</small></div>
        </div>
        <ul class="features">
          <li>Mauris pulvinar volutpat ipsum</li><li>Phasellus congue dapibus</li><li>Duis congue mauris nec</li><li>Curabitur dignissim malesuad</li><li>Vestibulum id scelerisque</li>
        </ul>
        <a class="btn btn-signup" href="#">Sign Up Now</a>
      </article>
      <article class="package">
        <div class="package-head">
          <div class="package-kicker">Broadcast</div>
          <div class="package-name">Package C</div>
          <div class="package-price">$35<small>/mo</small></div>
        </div>
        <ul class="features">
          <li>Integer sapien felis</li><li>Vivamus tempus quam et risuas</li><li>Etiam rutrum justo cursus</li><li>Pellentesque magna orci</li><li>Fusce in eros non orci</li>
        </ul>
        <a class="btn btn-signup" href="#">Sign Up Now</a>
      </article>
    </div>
  </section>

  <section class="contact">
    <h2 class="contact-title">Contact Us</h2>
    <p class="address">
      <svg class="icon" width="12" height="16" viewBox="0 0 12 16" aria-hidden="true"><path d="M6 0a6 6 0 0 0-6 6c0 4.5 6 10 6 10s6-5.5 6-10a6 6 0 0 0-6-6zm0 8.5A2.5 2.5 0 1 1 6 3.5a2.5 2.5 0 0 1 0 5z"/></svg>
      24 Building name, Street name, City Zipcode
    </p>
    <p class="reach">
      <span><svg class="icon" width="24" height="24" viewBox="0 0 24 24" aria-hidden="true"><path d="M6.6 10.8a15.1 15.1 0 0 0 6.6 6.6l2.2-2.2c.3-.3.7-.4 1-.2 1.1.4 2.3.6 3.6.6.6 0 1 .4 1 1V20c0 .6-.4 1-1 1A17 17 0 0 1 3 4c0-.6.4-1 1-1h3.5c.6 0 1 .4 1 1 0 1.3.2 2.5.6 3.6.1.3 0 .7-.2 1z"/></svg> 555 013 2648</span>
      <span><svg class="icon" width="26" height="20" viewBox="0 0 26 20" aria-hidden="true"><path d="M0 2a2 2 0 0 1 2-2h22a2 2 0 0 1 2 2v1L13 11 0 3zm0 3.5 13 8 13-8V18a2 2 0 0 1-2 2H2a2 2 0 0 1-2-2z"/></svg> info@rotorlinemedia.com</span>
    </p>
    <a class="btn btn-subscribe" href="#">Subscribe Now</a>
  </section>
</main>

<footer class="site-footer">
  <span>Copyright &copy; 2018 Rotorline Media Inc. &nbsp;All rights reserved.</span>
  <div class="social">
    <span role="img" aria-label="Social profile"></span>
    <span role="img" aria-label="Social profile"></span>
  </div>
</footer>
</body>
</html>
```